New Bottle Label for our Velinto Grand Reserva Brandy

Graphic Design Brief
We need a new bottle label for our Brandy Gran Reserva that we want to bring to the market.
Please have a look at all our current bottles and labels and the feel of our company under www.velinto-example.ch. We would like the design to be still different to the rest - as it is not a whisky, not a fruit product, not a spirit like a gin, thus we need to create like a new family, but still fitting in with the rest of the products.
The bottle that we will be using for the brand is a different one than the one that we already have, the design of the bottle is attached with a document.
I have also attached a briefing in regards to Brandy in general for your information.
### 1. What is Brandy?
Brandy is a distilled spirit made from fermented wine or other fruit wines. It is traditionally aged in oak barrels, which gives it its characteristic color and rich flavor. The aging process in oak is essential for developing the aromas and quality of the brandy.
### 2. What is Brandy Reserva?
A Brandy labeled as "Reserva" has undergone a longer aging process, typically at least 2 to 3 years, in oak barrels. This aging gives the brandy a deeper, more complex flavor profile and a darker color. "Reserva" is often an indication of higher quality.
### 3. Who enjoys drinking Brandy?
Brandy is typically favored by those who appreciate a deep, rich tasting experience. This often includes older consumers who value the time-aged complexity of the spirit. However, Brandy is also gaining popularity among younger people, especially through cocktails and modern serving styles.
### 4. Why is Brandy trending?
Brandy is experiencing a resurgence as consumers increasingly value quality and artisanal production methods. Its versatility in cocktails and association with traditional, luxurious experiences have also contributed to its renewed popularity.
### 5. What colors would be associated with Brandy?
The typical colors associated with Brandy are warm gold, amber, and deep golden-brown tones. These colors reflect the aging process in oak barrels and the richness of the flavors. Other associated colors might include dark brown and mahogany.
### 6. What is important to customers when buying Brandy?
Customers care about the origin of the Brandy, the aging time, the quality of the ingredients, the production method, and the brand. They also pay attention to the prestige of the product and the authenticity of the production.
### 7. What is not important to customers when buying Brandy?
For many customers, the price and packaging (unless it’s especially exclusive) may be less important than the quality and taste of the Brandy. The distillery name might be less significant if it isn’t tied to a particular reputation.
### 8. What do customers know about Swiss Brandy?
Swiss Brandy is still relatively unknown in many markets, but customers who are familiar with it appreciate the precision and quality of Swiss production. Swiss Brandy is assumed to be made with care and under strict quality standards.
### 9. What is Brandy Gran Reserva?
**Brandy Gran Reserva** is an even higher quality and longer-aged version of Brandy. Generally, a Gran Reserva is aged for at least 5 to 10 years or more in oak barrels. This extended aging process gives the Brandy an especially deep, complex flavor profile and often a darker, richer color. Gran Reserva is often regarded as the top-tier product within a Brandy range and appeals to discerning consumers who value quality, refinement, and a luxurious tasting experience.
The label “Gran Reserva” thus indicates the highest quality level for Brandies, similar to other spirits (like wine or whisky), where the aging time is a critical factor.
We age our Brandy Gran Reserva in the Solara way.
### 10. What emotions are associated with Brandy?
Brandy is often associated with luxury, relaxation, and comfort. It evokes feelings of tradition, elegance, and sophistication. Drinking Brandy is frequently seen as a moment of reflection and enjoyment.
### 11. How should Brandy be marketed?
Brandy should be marketed with a focus on its artisanal production, quality, and tradition. A narrative around the product, its aging, and origin can help create an emotional connection with the customer. The marketing should also emphasize the versatility of Brandy, whether consumed neat or in cocktails.
**Label design**:
The label should reflect the exclusivity of the product, with an elegant, minimalist design. The label should include information about the aging time, the use of oak barrels, and a brief story about the Brandy’s production.
we would like to have a modern look to the whole deisgn of the brandy
Target Market(s)
Customers that like Brandy
Target Market(s)
Switzerland
Industry/Entity Type
Distillery
Look and feel

```html
<!DOCTYPE html>
<html lang="en">
<head>
<meta charset="utf-8">
<title>Velinto Grand Reserva Brandy – Label</title>
<link href="https://fonts.googleapis.com/css2?family=Oswald:wght@300;400;500;600&family=Libre+Baskerville&family=Montserrat:wght@400&display=swap" rel="stylesheet">
<style>
  :root {
    --navy: #020f26;
    --white: #ffffff;
    --gold-dark: #a8742d;
    --gold-mid: #d9a13a;
    --gold-light: #ffe066;
    --bg: #ffffff;
  }
  html, body {
    margin: 0;
    padding: 0;
    width: 1200px;
    height: 1200px;
    overflow: hidden;
    background: var(--bg);
  }
  .canvas {
    position: relative;
    width: 1200px;
    height: 1200px;
  }
  .label {
    position: absolute;
    left: 394px;
    top: 93px;
    width: 412px;
    height: 1014px;
  }
  .label-body { fill: var(--navy); }
  .label-band { fill: var(--navy); }
  .label-border { fill: none; stroke: url(#gold); stroke-width: 4; }
  .rule { stroke: url(#gold); stroke-width: 2.5; }
  .brand-name {
    font-family: "Oswald", sans-serif;
    font-weight: 500;
    font-size: 112px;
    fill: var(--white);
    letter-spacing: 2px;
  }
  .grade, .strength {
    font-family: "Oswald", sans-serif;
    font-weight: 300;
    font-size: 72px;
    fill: var(--white);
    letter-spacing: 3px;
  }
  .product {
    font-family: "Oswald", sans-serif;
    font-weight: 500;
    font-size: 250px;
    fill: url(#gold-text);
  }
  .website {
    font-family: "Libre Baskerville", serif;
    font-size: 19px;
    fill: var(--white);
    letter-spacing: 3px;
  }
  .volume {
    font-family: "Montserrat", sans-serif;
    font-size: 22px;
    fill: var(--white);
  }
  .divider { stroke: var(--white); stroke-width: 1.5; }
</style>
</head>
<body>
<main class="canvas">
  <svg class="label" viewBox="0 0 572 1408" xmlns="http://www.w3.org/2000/svg" aria-label="Velinto Grand Reserva Brandy bottle label">
    <defs>
      <linearGradient id="gold" x1="0" y1="0" x2="1" y2="0">
        <stop offset="0" stop-color="#a8742d"/>
        <stop offset="0.5" stop-color="#ffd24a"/>
        <stop offset="1" stop-color="#a8742d"/>
      </linearGradient>
      <linearGradient id="gold-text" x1="0" y1="0" x2="1" y2="0">
        <stop offset="0" stop-color="#f2b53c"/>
        <stop offset="0.25" stop-color="#a8612f"/>
        <stop offset="0.45" stop-color="#d99a3a"/>
        <stop offset="0.58" stop-color="#ffe066"/>
        <stop offset="0.78" stop-color="#b6793a"/>
        <stop offset="1" stop-color="#e3b04a"/>
      </linearGradient>
    </defs>

    <path class="label-body" d="M0,55 Q286,-55 572,55 C560,250 535,420 527,600 L527,800 C535,1000 560,1180 572,1340 Q286,1476 0,1340 C12,1180 37,1000 45,800 L45,600 C37,420 12,250 0,55 Z"/>
    <path class="label-border" d="M16,70 Q286,-28 556,70 C545,250 522,420 514,600 L514,800 C522,1000 545,1180 556,1325 Q286,1448 16,1325 C27,1180 50,1000 58,800 L58,600 C50,420 27,250 16,70 Z"/>
    <rect class="label-band" x="5" y="553" width="562" height="297" rx="40"/>

    <text class="brand-name" x="286" y="240" text-anchor="middle">Velinto</text>

    <text class="grade" x="286" y="455" text-anchor="middle" textLength="350" lengthAdjust="spacingAndGlyphs">GRAND RESERVA</text>
    <line class="rule" x1="170" y1="549" x2="425" y2="549"/>

    <text class="product" x="286" y="795" text-anchor="middle" textLength="475" lengthAdjust="spacingAndGlyphs">BRANDY</text>

    <line class="rule" x1="165" y1="855" x2="410" y2="855"/>
    <text class="strength" x="286" y="1020" text-anchor="middle" textLength="308" lengthAdjust="spacingAndGlyphs">CASK TRENGTH</text>

    <text class="website" x="286" y="1158" text-anchor="middle">www.velinto-example.ch</text>

    <text class="volume" x="260" y="1339" text-anchor="end">25%</text>
    <line class="divider" x1="275" y1="1316" x2="275" y2="1346"/>
    <text class="volume" x="290" y="1339" text-anchor="start">350ml</text>
  </svg>
</main>
</body>
</html>
```